business card

Business card for new business.
Red and black corporate colors.
Card can have an Indsutrial feel to it. Feel free to add Rust, Bolted steel, or graphics as you see fit. We provide highly specialized services to the below mentioned industries.
Keep information out of corners so that if I want I can choose rounded corners.
Information
- front. name - title - phone - email
- Rear
Refining - Rail - Infrastructure - Mining - Energy
Calgary - Edmonton - Fort McMurray - Revelstoke - Vancouver

```html
<!DOCTYPE html>
<html lang="en">
<head>
<meta charset="utf-8">
<title>Girderline business card</title>
<link rel="stylesheet" href="https://fonts.googleapis.com/css2?family=Oswald:wght@500&family=Roboto:wght@400;700&family=Roboto+Condensed:wght@700&display=swap">
<style>
  :root {
    --backdrop: #6f4a31;
    --card-dark: #1a1a1b;
    --card-mid: #333335;
    --brand-red: #e30613;
    --text-white: #ffffff;
    --text-grey: #8c8c8c;
  }
  * { box-sizing: border-box; margin: 0; padding: 0; }
  html, body { width: 1200px; height: 960px; overflow: hidden; }
  body {
    background: var(--backdrop);
    position: relative;
    font-family: "Roboto", Arial, sans-serif;
  }
  .card {
    position: absolute;
    left: 300px;
    width: 600px;
    height: 342px;
    overflow: hidden;
    box-shadow: 0 2px 6px rgba(0,0,0,0.45);
  }
  .card--front { top: 130px; }
  .card--back { top: 489px; }
  .card-texture {
    position: absolute;
    inset: 0;
    background:
      linear-gradient(180deg, #0b0b0c 0%, transparent 18%, transparent 80%, #0b0b0c 100%),
      radial-gradient(ellipse at 50% 50%, var(--card-mid) 0%, var(--card-dark) 75%);
  }
  .brand {
    position: absolute;
    left: 64px;
    top: 82px;
    display: flex;
    align-items: center;
    gap: 10px;
  }
  .brand-square {
    width: 14px;
    height: 14px;
    background: var(--brand-red);
  }
  .brand-name {
    font-family: "Roboto Condensed", "Arial Narrow", sans-serif;
    font-weight: 700;
    font-size: 36px;
    line-height: 44px;
    color: var(--text-grey);
  }
  .person-name {
    position: absolute;
    left: 64px;
    top: 146px;
    font-family: "Oswald", Impact, sans-serif;
    font-weight: 500;
    font-size: 27px;
    line-height: 32px;
    color: var(--brand-red);
  }
  .person-title {
    position: absolute;
    left: 64px;
    top: 179px;
    font-size: 16px;
    line-height: 20px;
    color: var(--text-grey);
  }
  .contacts {
    position: absolute;
    left: 64px;
    top: 207px;
    list-style: none;
  }
  .contact {
    display: flex;
    align-items: center;
    gap: 9px;
    height: 19px;
    font-size: 14px;
    color: var(--text-white);
  }
  .contact svg { width: 13px; height: 13px; fill: var(--brand-red); }
  .services {
    position: absolute;
    left: 388px;
    top: 76px;
    list-style: none;
  }
  .service {
    position: relative;
    padding-left: 11px;
    height: 19px;
    line-height: 19px;
    font-weight: 700;
    font-size: 14px;
    color: var(--text-white);
  }
  .service::before {
    content: "";
    position: absolute;
    left: 0;
    top: 7px;
    width: 4px;
    height: 4px;
    border-radius: 50%;
    background: var(--brand-red);
  }
  .back-brand {
    position: absolute;
    inset: 0;
    display: flex;
    align-items: center;
    justify-content: center;
    font-family: "Roboto Condensed", "Arial Narrow", sans-serif;
    font-weight: 700;
    font-size: 40px;
    color: var(--brand-red);
  }
</style>
</head>
<body>
  <section class="card card--front">
    <div class="card-texture" role="img" aria-label="Distressed dark steel texture"></div>
    <div class="brand">
      <span class="brand-square"></span>
      <span class="brand-name">GIRDERLINE</span>
    </div>
    <h1 class="person-name">DANIEL MARSH</h1>
    <p class="person-title">CEO/FOUNDER</p>
    <ul class="contacts">
      <li class="contact">
        <svg viewBox="0 0 24 24"><path d="M6.6 10.8a15.1 15.1 0 0 0 6.6 6.6l2.2-2.2a1 1 0 0 1 1-.25 11.4 11.4 0 0 0 3.6.6 1 1 0 0 1 1 1V20a1 1 0 0 1-1 1A17 17 0 0 1 3 4a1 1 0 0 1 1-1h3.5a1 1 0 0 1 1 1c0 1.25.2 2.45.6 3.6a1 1 0 0 1-.25 1z"/></svg>
        555 014 2290
      </li>
      <li class="contact">
        <svg viewBox="0 0 24 24"><path d="M2 5h20v2l-10 6L2 7z M2 9l10 6 10-6v10H2z"/></svg>
        info@girderline.com
      </li>
      <li class="contact">
        <svg viewBox="0 0 24 24"><circle cx="12" cy="12" r="10"/></svg>
        www.girderline.com
      </li>
    </ul>
    <ul class="services">
      <li class="service">REFINING</li>
      <li class="service">RAIL</li>
      <li class="service">INFRASTRUCTURE</li>
      <li class="service">MINING</li>
      <li class="service">ENERGY</li>
      <li class="service">CALGARY</li>
      <li class="service">EDMONTON</li>
      <li class="service">FORT MCMURRAY</li>
      <li class="service">REVELSTOKE</li>
      <li class="service">VANCOUVER</li>
    </ul>
  </section>

  <section class="card card--back">
    <div class="card-texture" role="img" aria-label="Distressed dark steel texture"></div>
    <div class="back-brand">GIRDERLINE</div>
  </section>
</body>
</html>
```